Label and packaging - Lune de Sable

We are after label and pack design for a product called Lune de Sable. This product is a blend of Pinot Gris and Apple Cider.

Lune de Sable:

The packaging needs to accomplish the following: quickly explain what the product is, establish as a premium price product and grab the eye. The package should also reflect the product innovation.

Quickly Explain What the Product Is:

Lune de Sable is a nice name that could lift the image – but no one will have any idea what the product is by the name. Consider that a consumer will be staring at a shelf, then the bottle for maybe two to three seconds before moving on to another bottle. In those three seconds we need to make certain that they understand that the product is a blend of wine and cider. Lune de Sable will not support this on its own.

Suggestion is to use words like Wine, Cider, Orchard, Vine, Apple, Heirloom, Exotic and make it simple. Perhaps a sticker that says “50% Wine/50% Apple Cider” that sits on the neck of every bottle. They need to quickly ‘get it”. Imagery will assist as well. Consider a hybrid 50/50 image of wine grapes and apples to tell the story.

Establish a Premium Price Point:

The label needs to say high quality in the package and the font. Have fun with the shipper – this is where you can have a field day with imagery and fun buzz words – we love the idea of a busy shipper that tells the story with a clean and smart looking bottle.

Target Market(s)

This is a premium product targeted at females of age 25-45.

Industry/Entity Type

Consumer

Colors
ec1f27
9bcb3c

Requirements
Must have
• Label design on a burgundy bottle with a screw cap, see here for bottle shape: http://www.vk-flaskrange.co.nz/wine/#/?view=thumbs&segments=41&colors=&capacityMin=187&capacityMax=750&heightMin=171&heightMax=334&labelMin=44&labelMax=168&neckMin=0&neckMax=1000

Packaging design on a 12 x 750ml carton. This sort of thing: https://www.barrelnook.com.au/images/photo06.jpg

Nice to have
• We have attached some examples of a concept we quite like but it's not bright enough.

```html
<!DOCTYPE html>
<html lang="en">
<head>
<meta charset="utf-8">
<title>Lune de Sable – Bottle Label</title>
<link href="https://fonts.googleapis.com/css2?family=Tenor+Sans&family=Open+Sans:wght@400;600&display=swap" rel="stylesheet">
<style>
  :root {
    --page-bg: #f4f3f1;
    --label-bg: #fdfcf8;
    --label-edge: #e4e1d8;
    --ink: #5e5a56;
    --ink-soft: #8a857f;
    --rule: #b9b4ac;
    --band-green: #9fb98a;
    --band-text: #ffffff;
    --art-apple: #f0b07e;
    --art-grape: #b3a6d4;
    --art-wash: #f3eddd;
  }
  * { margin: 0; padding: 0; box-sizing: border-box; }
  html, body {
    width: 1196px;
    height: 1200px;
    overflow: hidden;
    background: var(--page-bg);
  }
  .canvas {
    width: 1196px;
    height: 1200px;
    display: flex;
    align-items: center;
    justify-content: center;
  }
  .label {
    width: 620px;
    height: 1060px;
    background: var(--label-bg);
    border: 1px solid var(--label-edge);
    box-shadow: 0 6px 24px rgba(0,0,0,0.08);
    display: flex;
    flex-direction: column;
    align-items: center;
  }
  .label__artwork {
    margin-top: 90px;
    width: 440px;
    height: 480px;
    background: linear-gradient(150deg, var(--art-apple) 0%, var(--art-wash) 50%, var(--art-grape) 100%);
  }
  .label__vintage {
    margin-top: 60px;
    font-family: "Tenor Sans", sans-serif;
    font-size: 26px;
    letter-spacing: 2px;
    color: var(--ink-soft);
  }
  .label__rule {
    margin-top: 12px;
    width: 330px;
    height: 2px;
    background: var(--rule);
  }
  .label__name {
    margin-top: 18px;
    font-family: "Tenor Sans", sans-serif;
    font-weight: 400;
    font-size: 62px;
    letter-spacing: 3px;
    line-height: 1.1;
    color: var(--ink);
    text-transform: uppercase;
    white-space: nowrap;
  }
  .label__name-small {
    font-size: 40px;
    text-transform: none;
    letter-spacing: 1px;
  }
  .label__blend {
    margin-top: 14px;
    width: 420px;
    font-family: "Open Sans", sans-serif;
    font-size: 27px;
    line-height: 1.2;
    color: var(--ink-soft);
  }
  .label__region {
    margin-top: 34px;
    width: 100%;
    height: 46px;
    background: var(--band-green);
    display: flex;
    align-items: center;
    justify-content: center;
    font-family: "Open Sans", sans-serif;
    font-weight: 600;
    font-size: 20px;
    letter-spacing: 2px;
    color: var(--band-text);
    text-transform: uppercase;
  }
  .label__facts {
    margin-top: 44px;
    display: flex;
    gap: 60px;
    font-family: "Open Sans", sans-serif;
    font-size: 26px;
    color: var(--ink);
  }
</style>
</head>
<body>
  <main class="canvas">
    <article class="label">
      <div class="label__artwork" role="img" aria-label="Painted illustration of an orange apple with a bunch of purple grapes and green leaves over a cream brush-stroke wash"></div>
      <p class="label__vintage">2011</p>
      <div class="label__rule"></div>
      <h1 class="label__name">Lune <span class="label__name-small">de</span> Sable</h1>
      <p class="label__blend">blend of apple cider<br>&amp; pinot gris</p>
      <p class="label__region">Marlborough · New Zealand</p>
      <p class="label__facts"><span>750 ml</span><span>14,7%vol</span></p>
    </article>
  </main>
</body>
</html>
```